i need a business card design for my family investment company "quorin investments" based in dubai. its a diverse investment firm focusing on education, hospitality and automotive. the design has to be modern and try to incorporate the logo "E" in the design. details on card as follow

Yusuf K Bin Tarrah
Managing Director
yusuf@quorin-mail.ae
www.quorin-mail.ae

Harbor district,palwick tower, office 2212, dubai
tel. 04 3850927
mobile.050 9184203

card used for networking events and investor meetings

Hospitality

```html
<!DOCTYPE html>
<html lang="en">
<head>
<meta charset="utf-8">
<title>Quorin Investments – Business Card</title>
<link href="https://fonts.googleapis.com/css2?family=Cinzel:wght@400;700&family=Josefin+Sans:wght@300&display=swap" rel="stylesheet">
<style>
  :root {
    --backdrop: #e6e6e6;
    --paper: #f7f7f6;
    --ink: #1f2a33;
    --brand-blue: #3f6384;
    --brand-blue-light: #5b7f9b;
    --brand-blue-dark: #2d4f70;
    --white: #ffffff;
  }
  * { box-sizing: border-box; margin: 0; padding: 0; }
  html, body {
    width: 1200px; height: 720px; overflow: hidden;
    background: var(--backdrop);
  }
  .canvas { position: relative; width: 1200px; height: 720px; }

  .card {
    position: absolute; top: 242px;
    width: 420px; height: 240px; overflow: hidden;
  }
  .card--front { left: 147px; background: var(--paper); }
  .card--back {
    left: 633px;
    background: linear-gradient(135deg, var(--brand-blue-light) 0%, var(--brand-blue) 50%, var(--brand-blue-dark) 100%);
  }

  .wordmark {
    position: absolute;
    font-family: "Josefin Sans", sans-serif; font-weight: 300;
    text-transform: uppercase; line-height: 1; text-align: center;
    white-space: nowrap;
  }
  .wordmark__name { display: block; letter-spacing: 0.5em; padding-left: 0.5em; }
  .wordmark__sub { display: block; letter-spacing: 1em; padding-left: 1em; }

  .card--front .wordmark { left: 10px; top: 96px; width: 220px; color: var(--ink); }
  .card--front .wordmark__name { font-size: 30px; }
  .card--front .wordmark__sub { font-size: 11px; margin-top: 7px; }

  .card--back .wordmark { left: 60px; top: 90px; width: 300px; color: var(--white); }
  .card--back .wordmark__name { font-size: 40px; }
  .card--back .wordmark__sub { font-size: 16px; margin-top: 8px; }

  .contact {
    position: absolute; left: 262px; top: 58px; width: 152px;
    font-family: "Cinzel", serif; color: var(--ink);
  }
  .contact__name { font-size: 11.5px; font-weight: 700; color: var(--brand-blue); line-height: 1.15; white-space: nowrap; }
  .contact__role { font-size: 9px; line-height: 1.3; }
  .contact__address { font-size: 8.5px; line-height: 1.3; margin-top: 10px; }
  .contact__list { list-style: none; margin-top: 12px; }
  .contact__item { display: flex; align-items: center; font-size: 8.5px; line-height: 12px; white-space: nowrap; }
  .contact__icon { width: 10px; height: 10px; margin-right: 8px; fill: var(--brand-blue); flex: none; }

  .footer-band {
    position: absolute; left: 0; bottom: 0; width: 420px; height: 17px;
    background: var(--brand-blue);
  }
  .footer-band__gap { position: absolute; top: 0; width: 6px; height: 17px; background: var(--white); }
</style>
</head>
<body>
<main class="canvas">
  <section class="card card--front" aria-label="Card front">
    <div class="wordmark">
      <span class="wordmark__name">Quorin</span>
      <span class="wordmark__sub">Investments</span>
    </div>

    <div class="contact">
      <p class="contact__name">Yusuf K Bin Tarrah</p>
      <p class="contact__role">Managing Director</p>
      <p class="contact__address">Harbor district, palwick tower,<br>office 2212, dubai</p>
      <ul class="contact__list">
        <li class="contact__item">
          <svg class="contact__icon" viewBox="0 0 10 10"><path d="M1 3 C1 1.5 9 1.5 9 3 L8 4 L6.5 3.5 L6.5 2.8 C5.5 2.5 4.5 2.5 3.5 2.8 L3.5 3.5 L2 4 Z M2.5 5 H7.5 L8.5 9 H1.5 Z"/></svg>
          Tel. 04 3850927
        </li>
        <li class="contact__item">
          <svg class="contact__icon" viewBox="0 0 10 10"><path d="M3 0.5 H7 A0.8 0.8 0 0 1 7.8 1.3 V8.7 A0.8 0.8 0 0 1 7 9.5 H3 A0.8 0.8 0 0 1 2.2 8.7 V1.3 A0.8 0.8 0 0 1 3 0.5 Z M3.1 1.6 V7.6 H6.9 V1.6 Z"/></svg>
          Mobile. 050 9184203
        </li>
        <li class="contact__item">
          <svg class="contact__icon" viewBox="0 0 10 10"><path d="M0.5 2 H9.5 V8 H0.5 Z M1.2 2.6 L5 5.6 L8.8 2.6 V2.5 H1.2 Z" fill-rule="evenodd"/></svg>
          yusuf@quorin-mail.ae
        </li>
        <li class="contact__item">
          <svg class="contact__icon" viewBox="0 0 10 10"><path d="M0.5 1.5 H9.5 V7 H0.5 Z M1.3 2.2 V6.3 H8.7 V2.2 Z M4.2 7 H5.8 V8.2 H7 V9 H3 V8.2 H4.2 Z" fill-rule="evenodd"/></svg>
          www.quorin-mail.ae
        </li>
      </ul>
    </div>

    <div class="footer-band">
      <span class="footer-band__gap" style="left:253px"></span>
      <span class="footer-band__gap" style="left:301px"></span>
      <span class="footer-band__gap" style="left:356px"></span>
    </div>
  </section>

  <section class="card card--back" aria-label="Card back">
    <div class="wordmark">
      <span class="wordmark__name">Quorin</span>
      <span class="wordmark__sub">Investments</span>
    </div>
  </section>
</main>
</body>
</html>
```